Business Card for my New Brokerage

Looking to get a business card design for my new Real Estate Brokerage.
I want it with Picture, Phone Number, Email, Website, Office Address
Name and Designation. Please add logo too.

Target Market(s)

Real Estate Investors or Home Buyers

Industry/Entity Type

Real Estate

Contact Information for Business Card

Name, Email, Phone Number, website, email, office address

Colors
EB3D1F
EC4F4E
F09395
F8D3D4
FCEDEE

Requirements
Must have
• Minimalistic, Clean, Modern, Photo
Nice to have
• White and Red Colors

```html
<!DOCTYPE html>
<html lang="en">
<head>
<meta charset="utf-8">
<title>Beacon Realty Inc – Business Card</title>
<link href="https://fonts.googleapis.com/css2?family=Montserrat:wght@400;500;700&display=swap" rel="stylesheet">
<style>
  :root {
    --brand-red: #e00000;
    --deep-red: #b30000;
    --panel-black: #222222;
    --gold: #d4b062;
    --white: #ffffff;
    --blush: #f8d3d4;
    --page: #2b2b2b;
  }
  * { margin: 0; padding: 0; box-sizing: border-box; }
  html, body { width: 1200px; height: 900px; overflow: hidden; }
  body {
    background: var(--page);
    font-family: "Montserrat", sans-serif;
    display: flex;
    flex-direction: column;
    align-items: center;
    justify-content: center;
    gap: 40px;
  }
  .card {
    position: relative;
    width: 700px;
    height: 400px;
    border-radius: 24px;
    overflow: hidden;
    background: var(--brand-red);
    color: var(--white);
    box-shadow: 0 10px 30px rgba(0,0,0,0.45);
  }
  .card-shapes { position: absolute; inset: 0; }

  /* front */
  .wordmark {
    position: absolute;
    left: 150px;
    top: 58px;
    color: var(--brand-red);
    font-weight: 700;
    line-height: 1;
  }
  .wordmark .wordmark-main { display: block; font-size: 54px; letter-spacing: 2px; }
  .wordmark .wordmark-sub { display: block; font-size: 17px; letter-spacing: 7px; margin-top: 8px; }

  .portrait {
    position: absolute;
    left: 468px;
    top: 84px;
    width: 184px;
    height: 184px;
    border-radius: 50%;
    border: 3px solid var(--brand-red);
    background: radial-gradient(circle at 50% 40%, #d9c7bb 0%, #f4f1ee 55%, #ffffff 100%);
  }

  .office-address {
    position: absolute;
    left: 40px;
    top: 205px;
    font-size: 15px;
    line-height: 1.45;
  }

  .contact-block {
    position: absolute;
    right: 44px;
    top: 282px;
    text-align: right;
  }
  .person-name { font-size: 25px; font-weight: 700; letter-spacing: 1.5px; }
  .person-role { font-size: 15px; margin-bottom: 6px; }
  .contact-line {
    display: flex;
    justify-content: flex-end;
    align-items: center;
    gap: 6px;
    font-size: 14px;
    line-height: 1.4;
  }
  .contact-line svg { width: 13px; height: 13px; flex: none; }

  /* back */
  .card-back { display: flex; align-items: center; justify-content: center; }
  .back-wordmark {
    color: var(--blush);
    font-weight: 700;
    text-align: center;
    line-height: 1;
  }
  .back-wordmark .wordmark-main { display: block; font-size: 74px; letter-spacing: 3px; }
  .back-wordmark .wordmark-sub { display: block; font-size: 22px; letter-spacing: 10px; margin-top: 12px; }
</style>
</head>
<body>

  <section class="card card-front">
    <svg class="card-shapes" viewBox="0 0 700 400" aria-hidden="true">
      <path d="M150,0 H700 V300 C660,262 610,240 540,236 C420,230 260,238 170,212 C110,194 90,150 105,70 C112,30 125,0 150,0 Z" fill="var(--panel-black)"/>
      <path d="M72,118 C85,190 150,224 300,238 C420,248 540,244 610,262 C650,272 680,290 700,310" fill="none" stroke="var(--gold)" stroke-width="5"/>
      <path d="M86,104 C92,170 140,210 250,226" fill="none" stroke="var(--panel-black)" stroke-width="3"/>
    </svg>

    <div class="wordmark">
      <span class="wordmark-main">BEACON</span>
      <span class="wordmark-sub">REALTY INC</span>
    </div>

    <div class="portrait" role="img" aria-label="Portrait photo of the agent"></div>

    <p class="office-address">218 Maple Ridge Court<br>Fairview, GA 30512</p>

    <div class="contact-block">
      <p class="person-name">DANIEL REYES</p>
      <p class="person-role">Founder and President</p>
      <p class="contact-line">+330 555-0142
        <svg viewBox="0 0 16 16"><path d="M3 1.5h3l1.2 3.2-1.8 1.2a9 9 0 0 0 4.7 4.7l1.2-1.8 3.2 1.2v3a1.5 1.5 0 0 1-1.6 1.5A13 13 0 0 1 1.5 3.1 1.5 1.5 0 0 1 3 1.5z" fill="var(--white)"/></svg>
      </p>
      <p class="contact-line">info@beaconrealtyinc.com
        <svg viewBox="0 0 16 16"><rect x="1.5" y="3.5" width="13" height="9" rx="1" fill="none" stroke="var(--white)" stroke-width="1.5"/><path d="M2 4l6 5 6-5" fill="none" stroke="var(--white)" stroke-width="1.5"/></svg>
      </p>
      <p class="contact-line">www.beaconrealtyinc.com
        <svg viewBox="0 0 16 16"><circle cx="8" cy="8" r="6.5" fill="none" stroke="var(--white)" stroke-width="1.4"/><ellipse cx="8" cy="8" rx="2.8" ry="6.5" fill="none" stroke="var(--white)" stroke-width="1.2"/><path d="M1.5 8h13" stroke="var(--white)" stroke-width="1.2"/></svg>
      </p>
    </div>
  </section>

  <section class="card card-back">
    <div class="back-wordmark">
      <span class="wordmark-main">BEACON</span>
      <span class="wordmark-sub">REALTY INC</span>
    </div>
  </section>

</body>
</html>
```